Sales sheet for printing and embroidery apparel items - Copper Hollow Graphics

I would like a one page flyer or sales sheet that I would use as a template to send different images of apparel we produce. I have attached examples of layouts I like.
- Ideally, it would have space for 3-5 items.
- I would like it one page only - not a folding flyer.
- Our companies name is Copper Hollow Graphics.
- This will be used for many different products and markets so I don't need wording/copy. You can use wording from the 7M9 or T58 flyer.

Colors
0054AA
0677BA
7BADD7
CADEEF
E8F1F8
00AB8E
00BBA5
67D7C9
C6EFE9
E9F9F6
FFC000
F8CF3A
FAE287
FDF2CF
FEFAEE

Requirements
Must have
• Places for between 3 and 5 images of apparel (t-shirts, hats etc)

```html
<!DOCTYPE html>
<html lang="en">
<head>
<meta charset="utf-8">
<title>Copper Hollow Graphics – Sales Sheet</title>
<link rel="stylesheet" href="https://fonts.googleapis.com/css2?family=Saira:ital,wght@1,800;1,900&family=Roboto:wght@400;500;700&family=Teko:wght@500;600&display=swap">
<style>
  :root {
    --artboard: #b3b3b3;
    --paper: #ffffff;
    --navy: #0b3a73;
    --red: #d23d40;
    --red-bright: #ef4b4b;
    --white: #ffffff;
    --placeholder: #e1e1e1;
    --ink: #111111;
    --photo-light: #eceae6;
    --photo-mid: #c9c7c2;
  }
  * { box-sizing: border-box; margin: 0; padding: 0; }
  html, body { width: 906px; height: 1200px; overflow: hidden; }
  body { background: var(--artboard); font-family: "Roboto", sans-serif; position: relative; }

  .flyer {
    position: absolute; left: 155px; top: 158px;
    width: 576px; height: 864px;
    background: var(--paper); overflow: hidden;
  }
  .abs { position: absolute; }

  /* header */
  .brand { left: 90px; top: 18px; width: 140px; text-align: center; }
  .brand-mark { width: 36px; height: 36px; background: var(--navy); margin: 0 auto 6px; }
  .brand-name { font-weight: 700; font-size: 12px; line-height: 14px; color: var(--navy); white-space: nowrap; }

  .headline { left: 10px; top: 90px; font-family: "Saira", sans-serif; font-style: italic; font-weight: 900; line-height: 1; white-space: nowrap; }
  .headline .line-1 { color: var(--red-bright); font-size: 38px; letter-spacing: 0.6px; }
  .headline .line-2 { color: var(--navy); font-size: 42px; margin-top: -2px; }
  .headline .line-3 { color: var(--navy); font-size: 31px; margin-top: -3px; }

  .hero-photo { left: 0; top: 0; width: 576px; height: 205px; }

  /* bands */
  .band { left: 0; width: 576px; }
  .band-navy { background: var(--navy); }
  .band-red { background: var(--red); }
  .band::before, .band::after { content: ""; position: absolute; left: 0; right: 0; height: 10px; }
  .band-navy::before { top: -6px; background: linear-gradient(to bottom, rgba(11,58,115,0), rgba(11,58,115,0.85)); }
  .band-navy::after { bottom: -6px; background: linear-gradient(to top, rgba(11,58,115,0), rgba(11,58,115,0.85)); }
  .band-red::before { top: -6px; background: linear-gradient(to bottom, rgba(210,61,64,0), rgba(210,61,64,0.85)); }
  .band-red::after { bottom: -6px; background: linear-gradient(to top, rgba(210,61,64,0), rgba(210,61,64,0.85)); }

  .features { top: 200px; height: 122px; }
  .feature { position: absolute; top: 10px; width: 136px; margin-left: -68px; text-align: center; }
  .feature svg { display: block; margin: 0 auto; }
  .feature-title { font-family: "Saira", sans-serif; font-style: italic; font-weight: 800; font-size: 12.5px; color: var(--red-bright); margin-top: 8px; letter-spacing: 0.3px; white-space: nowrap; }
  .feature-text { font-size: 9px; line-height: 11px; color: var(--white); margin-top: 1px; }

  .section-title {
    position: absolute; left: 0; width: 576px; text-align: center;
    font-family: "Saira", sans-serif; font-style: italic; font-weight: 900; font-size: 22px; line-height: 26px; letter-spacing: 0.5px;
  }
  .section-title::after { content: ""; display: block; width: 58px; height: 1.5px; margin: 2px auto 0; }
  .title-red { color: var(--red); }
  .title-red::after { background: var(--navy); }
  .title-white { color: var(--white); }
  .title-white::after { background: var(--white); }

  /* products */
  .products-title { top: 328px; }
  .product-slot { top: 371px; width: 103px; height: 109px; background: var(--placeholder); }

  /* offer */
  .offer { top: 497px; height: 118px; }
  .offer-title { top: 20px; }
  .offer-item { position: absolute; top: 58px; height: 40px; display: flex; align-items: center; gap: 6px; color: var(--white); font-weight: 700; font-size: 10px; line-height: 12px; white-space: nowrap; }
  .offer-divider { position: absolute; top: 52px; width: 1px; height: 50px; background: rgba(255,255,255,0.6); }

  /* steps */
  .steps { top: 622px; height: 165px; }
  .steps-title { top: 14px; }
  .step { position: absolute; top: 56px; width: 160px; margin-left: -80px; text-align: center; }
  .step svg { display: block; margin: 0 auto; }
  .step-title { font-family: "Teko", sans-serif; font-weight: 600; font-size: 15px; line-height: 14px; color: var(--red-bright); margin-top: 6px; letter-spacing: 0.3px; }
  .step-text { font-size: 9px; line-height: 11px; color: var(--white); margin-top: 2px; }
  .step-arrow { position: absolute; top: 92px; }

  /* footer */
  .closing { left: 20px; top: 806px; font-family: "Teko", sans-serif; font-weight: 600; font-size: 24px; line-height: 24px; color: var(--navy); letter-spacing: 0.3px; white-space: nowrap; }
  .contact { top: 832px; height: 24px; display: flex; align-items: center; gap: 6px; white-space: nowrap; }
  .contact-phone { left: 13px; font-family: "Teko", sans-serif; font-weight: 600; font-size: 21px; line-height: 24px; color: var(--ink); }
  .contact-email { left: 142px; font-size: 12px; line-height: 24px; color: var(--ink); }
  .contact-icon { flex: none; width: 19px; height: 19px; border-radius: 50%; background: var(--red); display: flex; align-items: center; justify-content: center; }

  .badge { top: 811px; height: 24px; }
  .badge-circle { border-radius: 50%; background: #e6e6e6; border: 2px solid var(--red); }
  .badge-rect { background: #ecebf3; border-bottom: 3px solid #5b2d82; }
  .social { top: 840px; width: 13px; height: 13px; border-radius: 50%; background: var(--red); }
</style>
</head>
<body>
<main class="flyer">

  <svg class="abs hero-photo" viewBox="0 0 576 205">
    <defs>
      <linearGradient id="photoTone" x1="0" y1="0" x2="1" y2="1">
        <stop offset="0" stop-color="var(--photo-light)"/>
        <stop offset="0.55" stop-color="#dcdad6"/>
        <stop offset="1" stop-color="var(--photo-mid)"/>
      </linearGradient>
    </defs>
    <path role="img" aria-label="Product photo: branded backpack, water bottle, notebook, blanket and grey hoodie on a light wood table"
          d="M372 0 C330 40 318 105 360 145 C388 170 386 190 370 205 L576 205 L576 0 Z" fill="url(#photoTone)"/>
    <path d="M362 0 C318 42 305 108 350 148 C378 172 378 192 356 205" fill="none" stroke="var(--red)" stroke-width="3"/>
  </svg>

  <div class="abs brand">
    <div class="brand-mark"></div>
    <div class="brand-name">Copper Hollow Graphics</div>
  </div>

  <h1 class="abs headline">
    <div class="line-1">ORDER SHIRTS</div>
    <div class="line-2">FOR YOUR ALL</div>
    <div class="line-3">OF YOUR RETREATS</div>
  </h1>

  <section class="abs band band-navy features">
    <div class="feature" style="left:76px">
      <svg width="48" height="48" viewBox="0 0 48 48" fill="none" stroke="#fff" stroke-width="1.3">
        <path d="M6 18 L20 6 L30 6 L42 20 L30 34 L16 34 Z"/>
        <path d="M6 22 L16 38 L30 38 L42 24"/><path d="M6 26 L16 42 L30 42 L42 28"/>
        <path d="M20 6 C22 10 28 10 30 6"/>
      </svg>
      <div class="feature-title">LOW MINIMUMS</div>
      <div class="feature-text">Order as few as 24 pieces<br>to get started.</div>
    </div>
    <div class="feature" style="left:219px">
      <svg width="48" height="48" viewBox="0 0 48 48" fill="none" stroke="#fff" stroke-width="1.3">
        <path d="M4 6 L10 6 L22 38 L44 30"/><circle cx="23" cy="41" r="3"/>
        <rect x="18" y="12" width="14" height="12" transform="rotate(-20 25 18)"/>
        <rect x="24" y="8" width="10" height="9" transform="rotate(-20 29 12)"/>
        <path d="M2 26 H10 M4 31 H12 M6 36 H14"/>
      </svg>
      <div class="feature-title">FAST TURNAROUND</div>
      <div class="feature-text">2-week standard delivery.</div>
    </div>
    <div class="feature" style="left:366px">
      <svg width="52" height="48" viewBox="0 0 52 48" fill="none" stroke="#fff" stroke-width="1.3">
        <circle cx="26" cy="8" r="5"/><circle cx="15" cy="10" r="4"/><circle cx="37" cy="10" r="4"/><circle cx="6" cy="12" r="3"/><circle cx="46" cy="12" r="3"/>
        <path d="M18 42 V24 Q26 16 34 24 V42 M22 42 V30 M30 42 V30"/>
        <path d="M10 36 V22 Q15 17 19 20 M42 36 V22 Q37 17 33 20"/>
        <path d="M2 32 V22 Q5 19 9 21 M50 32 V22 Q47 19 43 21"/>
      </svg>
      <div class="feature-title">REAL PEOPLE</div>
      <div class="feature-text">Work with our team of<br>experts and artists.</div>
    </div>
    <div class="feature" style="left:507px">
      <svg width="52" height="48" viewBox="0 0 52 48" fill="none" stroke="#fff" stroke-width="1.3">
        <path d="M26 4 L36 8 V18 C36 25 31 29 26 31 C21 29 16 25 16 18 V8 Z"/>
        <path d="M21 17 L25 21 L31 14"/>
        <path d="M4 34 C10 30 18 32 24 36 H34 M14 40 C22 44 34 44 48 36"/>
        <path d="M8 10 L12 12 M44 10 L40 12 M6 20 H11 M46 20 H41"/>
      </svg>
      <div class="feature-title">GUARANTEED</div>
      <div class="feature-text">We promise accurate,<br>quality work.</div>
    </div>
  </section>

  <h2 class="section-title title-red products-title">OUR PRODUCTS</h2>
  <div class="abs product-slot" style="left:18px" role="img" aria-label="Product image slot 1"></div>
  <div class="abs product-slot" style="left:127px" role="img" aria-label="Product image slot 2"></div>
  <div class="abs product-slot" style="left:236px" role="img" aria-label="Product image slot 3"></div>
  <div class="abs product-slot" style="left:345px" role="img" aria-label="Product image slot 4"></div>
  <div class="abs product-slot" style="left:454px" role="img" aria-label="Product image slot 5"></div>

  <section class="abs band band-red offer">
    <h2 class="section-title title-white offer-title">WE OFFER</h2>
    <div class="offer-item" style="left:16px">
      <svg width="36" height="36" viewBox="0 0 36 36" fill="#fff">
        <path d="M18 4 L21 8 L26 6 L27 11 L32 13 L29 17 L32 21 L27 23 L26 28 L21 26 L18 31 L15 26 L10 28 L9 23 L4 21 L7 17 L4 13 L9 11 L10 6 L15 8 Z"/>
        <circle cx="18" cy="18" r="6" fill="var(--red)"/>
      </svg>
      Art Design
    </div>
    <div class="offer-divider" style="left:114px"></div>
    <div class="offer-item" style="left:124px">
      <svg width="38" height="26" viewBox="0 0 38 26" fill="#fff">
        <rect x="1" y="2" width="24" height="16" rx="1"/><path d="M26 7 H32 L37 13 V19 H26 Z"/>
        <circle cx="8" cy="21" r="3.5"/><circle cx="30" cy="21" r="3.5"/>
        <rect x="4" y="6" width="18" height="8" fill="var(--red)"/>
      </svg>
      Free Shipping
    </div>
    <div class="offer-divider" style="left:238px"></div>
    <div class="offer-item" style="left:256px">
      <svg width="30" height="32" viewBox="0 0 30 32" fill="#fff">
        <circle cx="18" cy="10" r="9"/>
        <text x="18" y="14.5" font-size="12" font-family="Roboto, sans-serif" font-weight="700" fill="var(--red)" text-anchor="middle">$</text>
        <rect x="1" y="22" width="4" height="9"/><path d="M6 23 H14 L20 21 L27 20 L27 23 L19 29 H6 Z"/>
      </svg>
      We Pay ALL Royalties<br>to the Movement
    </div>
    <div class="offer-divider" style="left:398px"></div>
    <div class="offer-item" style="left:414px">
      <svg width="32" height="30" viewBox="0 0 32 30" fill="#fff">
        <path d="M10 2 L13 5 H19 L22 2 L31 8 L27 14 L24 12 V29 H8 V12 L5 14 L1 8 Z"/>
      </svg>
      Many Options of Shirt<br>Styles and Colors
    </div>
  </section>

  <section class="abs band band-navy steps">
    <h2 class="section-title title-white steps-title">HOW TO START AN ORDER</h2>
    <div class="step" style="left:98px">
      <svg width="30" height="30" viewBox="0 0 30 30" fill="none" stroke="#fff" stroke-width="1.3">
        <circle cx="13" cy="13" r="11"/><path d="M21 21 L28 28"/>
        <path d="M6 15 V12 L8 9 H17 L20 12 V15 Z"/><circle cx="9" cy="16" r="1.5"/><circle cx="17" cy="16" r="1.5"/>
      </svg>
      <div class="step-title">CHOOSE YOUR RIDE</div>
      <div class="step-text">Send us a picture, or let us know the make and model of the vehicle you would like featured on your apparel.</div>
    </div>
    <svg class="step-arrow" style="left:173px" width="34" height="8" viewBox="0 0 34 8" fill="none" stroke="#fff" stroke-width="1.2"><path d="M0 4 H32 M28 1 L32 4 L28 7"/></svg>
    <div class="step" style="left:290px">
      <svg width="32" height="32" viewBox="0 0 32 32" fill="none" stroke="#fff" stroke-width="1.3">
        <path d="M11 2 L13 4 H19 L21 2 L30 7 L27 13 L24 11 V18 M8 20 V11 L5 13 L2 7 Z"/>
        <path d="M16 30 L13 23 C12 21 14 20 15 22 V14 C15 12 18 12 18 14 V19 L23 20 C25 21 25 23 24 26 L22 30"/>
      </svg>
      <div class="step-title">PICK YOUR GEAR</div>
      <div class="step-text">We will help you choose your t-shirts, sweatshirts or other apparel items and determine sizes and quantities.</div>
    </div>
    <svg class="step-arrow" style="left:376px" width="34" height="8" viewBox="0 0 34 8" fill="none" stroke="#fff" stroke-width="1.2"><path d="M0 4 H32 M28 1 L32 4 L28 7"/></svg>
    <div class="step" style="left:493px">
      <svg width="30" height="30" viewBox="0 0 30 30" fill="none" stroke="#fff" stroke-width="1.6">
        <path d="M4 26 L22 8 M20 4 L26 10 L24 12 L18 6 Z"/>
        <path d="M26 26 L8 8 M4 4 L9 3 L11 8 L8 11 L3 9 Z"/>
      </svg>
      <div class="step-title">WE CUSTOMIZE</div>
      <div class="step-text">We make the magic happen and our team of expert artists will design your shirts and get a proof out to you. Upon order</div>
    </div>
  </section>

  <div class="abs closing">WE’D LOVE TO WORK WITH YOU!</div>
  <div class="abs contact contact-phone">
    <span class="contact-icon"><svg width="11" height="11" viewBox="0 0 24 24" fill="#fff"><path d="M6.6 10.8c1.4 2.8 3.8 5.1 6.6 6.6l2.2-2.2c.3-.3.7-.4 1-.2 1.1.4 2.3.6 3.6.6.6 0 1 .4 1 1V20c0 .6-.4 1-1 1C10.6 21 3 13.4 3 4c0-.6.4-1 1-1h3.5c.6 0 1 .4 1 1 0 1.3.2 2.5.6 3.6.1.3 0 .7-.2 1z"/></svg></span>
    <span>555-014-2280</span>
  </div>
  <div class="abs contact contact-email">
    <span class="contact-icon"><svg width="11" height="11" viewBox="0 0 24 24" fill="#fff"><path d="M6.6 10.8c1.4 2.8 3.8 5.1 6.6 6.6l2.2-2.2c.3-.3.7-.4 1-.2 1.1.4 2.3.6 3.6.6.6 0 1 .4 1 1V20c0 .6-.4 1-1 1C10.6 21 3 13.4 3 4c0-.6.4-1 1-1h3.5c.6 0 1 .4 1 1 0 1.3.2 2.5.6 3.6.1.3 0 .7-.2 1z"/></svg></span>
    <span>avery@copperhollowtees.com</span>
  </div>

  <div class="abs badge badge-circle" style="left:339px;width:24px" role="img" aria-label="Certification badge"></div>
  <div class="abs badge badge-circle" style="left:371px;width:24px" role="img" aria-label="Certification badge"></div>
  <div class="abs badge badge-rect" style="left:401px;width:55px" role="img" aria-label="Certification badge"></div>
  <div class="abs badge" style="left:463px;width:34px;border-radius:50%;background:#e3eef8" role="img" aria-label="Listing badge"></div>
  <div class="abs badge" style="left:503px;width:27px;border-radius:50%;background:#3e9a3b" role="img" aria-label="Partner badge"></div>
  <div class="abs badge" style="left:536px;width:25px;background:#fbe8cf" role="img" aria-label="Partner badge"></div>

  <div class="abs social" style="left:514px" role="img" aria-label="Social link"></div>
  <div class="abs social" style="left:531px" role="img" aria-label="Social link"></div>
  <div class="abs social" style="left:548px" role="img" aria-label="Social link"></div>

</main>
</body>
</html>
```